Lanternfield Drinks business cards

We need a business card design for our new logo. The company is modern, progressive, professional, yet approachable. The key products are ready to drink bottles and cans of coffee based beverages.
These cards will be a critical part of the first impression made by our sales organization, business development team, and all external facing personnel.
Card can be a vertical or horizontal orientation.

Target Market(s)

Customers, suppliers, business partners

Industry/Entity Type

Business

Contact Information for Business Card

Business cards should feature Company Name and Logo.

Font styles to use
Serif

Colors

Designer to choose colors to be used in the design.

Requirements
Must have
• Strong readability of Name, phone #, mobile number and email address.
• Job title, website url, Street Address, and other details can be secondary level readability.
Nice to have
• High impact, simplistic quality design.
• Ok to utilize the 'H in the box' separate from the company name

```html
<!DOCTYPE html>
<html lang="en">
<head>
<meta charset="utf-8">
<title>Lanternfield Drinks – Business Cards</title>
<link href="https://fonts.googleapis.com/css2?family=Libre+Baskerville:wght@400;700&display=swap" rel="stylesheet">
<style>
  :root {
    --backdrop: #3a3a3c;
    --card: #1c1c1d;
    --accent: #e8542a;
    --text-light: #e9e6e1;
    --text-muted: #b9b5af;
  }
  * { margin: 0; padding: 0; box-sizing: border-box; }
  html, body { width: 800px; height: 1200px; overflow: hidden; }
  body {
    background: var(--backdrop);
    font-family: "Libre Baskerville", Georgia, serif;
    position: relative;
  }
  .card {
    position: absolute;
    left: 90px;
    width: 620px;
    height: 354px;
    background: var(--card);
    box-shadow: 0 14px 30px rgba(0,0,0,0.45);
  }
  .card--front { top: 120px; }
  .card--back { top: 720px; }

  .brand { display: flex; flex-direction: column; align-items: center; }
  .brand__square {
    width: 36px; height: 36px;
    border: 3px solid var(--accent);
    margin-bottom: 12px;
  }
  .brand__name {
    color: var(--accent);
    font-weight: 700;
    text-transform: uppercase;
    letter-spacing: 1px;
    line-height: 1.15;
    text-align: center;
  }

  .card--front .brand {
    position: absolute; top: 88px; left: 0; right: 0;
  }
  .card--front .brand__square { width: 44px; height: 44px; }
  .card--front .brand__name { font-size: 34px; }

  .front-url {
    position: absolute; top: 238px; left: 110px; right: 110px;
    display: flex; align-items: center; gap: 12px;
  }
  .front-url__rule { flex: 1; height: 2px; background: var(--accent); }
  .front-url__text { color: var(--text-light); font-size: 11px; letter-spacing: 0.5px; }

  .card--back .brand {
    position: absolute; top: 118px; left: 30px; width: 270px;
  }
  .card--back .brand__name { font-size: 24px; }

  .contact {
    position: absolute; top: 74px; left: 342px; right: 24px;
  }
  .contact__name { color: var(--accent); font-size: 17px; font-weight: 700; }
  .contact__title { color: var(--text-light); font-size: 11px; margin-top: 4px; }
  .contact__list { list-style: none; margin-top: 22px; }
  .contact__item {
    display: flex; align-items: center; gap: 12px;
    color: var(--text-light); font-size: 11px; line-height: 1.25;
    margin-bottom: 7px;
  }
  .contact__icon { width: 12px; height: 12px; flex: none; fill: var(--accent); }
</style>
</head>
<body>
  <section class="card card--front">
    <div class="brand">
      <div class="brand__square"></div>
      <div class="brand__name">Lanternfield Drinks</div>
    </div>
    <div class="front-url">
      <span class="front-url__rule"></span>
      <span class="front-url__text">www.lanternfielddrinks.com</span>
      <span class="front-url__rule"></span>
    </div>
  </section>

  <section class="card card--back">
    <div class="brand">
      <div class="brand__square"></div>
      <div class="brand__name">Lanternfield Drinks</div>
    </div>
    <div class="contact">
      <div class="contact__name">Jordan Ellis Reed</div>
      <div class="contact__title">Managing Director</div>
      <ul class="contact__list">
        <li class="contact__item">
          <svg class="contact__icon" viewBox="0 0 12 12"><path d="M6 0a4 4 0 0 0-4 4c0 3 4 8 4 8s4-5 4-8a4 4 0 0 0-4-4zm0 5.6a1.6 1.6 0 1 1 0-3.2 1.6 1.6 0 0 1 0 3.2z"/></svg>
          <span>418 Meadow Row,<br>Brookvale, ST 24680</span>
        </li>
        <li class="contact__item">
          <svg class="contact__icon" viewBox="0 0 12 12"><path d="M2.5 0.5l2 2.2-1 1.5a7 7 0 0 0 4.3 4.3l1.5-1 2.2 2-1.2 1.8C5 11 1 7 0.7 1.7z"/></svg>
          <span>555.555.5555</span>
        </li>
        <li class="contact__item">
          <svg class="contact__icon" viewBox="0 0 12 12"><rect x="3" y="0.5" width="6" height="11" rx="1.2"/></svg>
          <span>555.666.7777</span>
        </li>
        <li class="contact__item">
          <svg class="contact__icon" viewBox="0 0 12 12"><path d="M0 2h12v8H0z M0 2l6 4.5L12 2" stroke="#1c1c1d" stroke-width="0.8"/></svg>
          <span>jordan@lanternfield.com</span>
        </li>
        <li class="contact__item">
          <svg class="contact__icon" viewBox="0 0 12 12"><circle cx="6" cy="6" r="5.5"/><path d="M0.5 6h11M6 0.5c-2.5 3-2.5 8 0 11M6 0.5c2.5 3 2.5 8 0 11" stroke="#1c1c1d" stroke-width="0.8" fill="none"/></svg>
          <span>www.lanternfield.com</span>
        </li>
      </ul>
    </div>
  </section>
</body>
</html>
```